Keystone Trench Co Business Card*

Looking for a professional, clean and crisp business card

I am in the underground utilities industry and am just looking for a really impressive business card. I would like our card to be white with our symbol crisp and clear with it protruding. I also have a business partner that will require his name and info on the card once the design is set. I would like to have our website info on the card which is;
http://keystonetrenchco.example/

Contact Information for Business Card

Website, contact name, number and email

```html
<!DOCTYPE html>
<html lang="en">
<head>
<meta charset="utf-8">
<title>Keystone Trench Co – Business Card</title>
<link href="https://fonts.googleapis.com/css2?family=Roboto:wght@400;500&display=swap" rel="stylesheet">
<style>
  :root {
    --backdrop: #e9e8e6;
    --card: #2c2c2c;
    --card-edge: #3f63b8;
    --white: #ffffff;
    --accent-blue: #4a6cc4;
    --muted: #b9b9b9;
    --divider: #6a6a6a;
    --ridge-dark: #161616;
    --ridge-light: #8a8a8a;
  }
  * { box-sizing: border-box; margin: 0; padding: 0; }
  html, body {
    width: 1200px; height: 801px; overflow: hidden;
    background: var(--backdrop);
    font-family: "Roboto", Arial, sans-serif;
  }
  .sheet {
    width: 1200px; height: 801px;
    display: flex; align-items: center; justify-content: center; gap: 60px;
  }
  .card {
    position: relative;
    width: 530px; height: 303px;
    background: var(--card);
    border-bottom: 3px solid var(--card-edge);
    border-right: 2px solid var(--card-edge);
    box-shadow: 0 10px 24px rgba(0,0,0,.22);
    overflow: hidden;
  }

  /* Front */
  .front .brand {
    position: absolute; left: 0; right: 0; top: 62px;
    display: flex; align-items: center; justify-content: center; gap: 12px;
  }
  .brand-dot {
    width: 18px; height: 18px; border-radius: 50%;
    background: var(--white);
  }
  .brand-name {
    color: var(--white); font-weight: 500; font-size: 30px; letter-spacing: .5px;
  }
  .front .details {
    position: absolute; left: 0; right: 0; bottom: 52px;
    display: flex; align-items: center; justify-content: center; gap: 22px;
  }
  .person { text-align: right; }
  .person-name { color: var(--accent-blue); font-size: 22px; font-weight: 400; }
  .person-role { color: var(--muted); font-size: 13px; margin-top: 2px; }
  .rule { width: 1px; height: 62px; background: var(--divider); }
  .contacts { list-style: none; }
  .contacts li {
    display: flex; align-items: center; gap: 9px;
    color: var(--muted); font-size: 13px; line-height: 21px;
  }
  .contacts svg { width: 12px; height: 12px; flex: none; }

  /* Back */
  .back .brand {
    position: absolute; left: 0; right: 0; top: 58px;
    display: flex; align-items: center; justify-content: center; gap: 14px;
  }
  .back .brand-name { font-size: 40px; }
  .back .brand-dot { width: 22px; height: 22px; }
  .ridge-art {
    position: absolute; left: 0; right: 0; bottom: 0; height: 160px;
  }
</style>
</head>
<body>
<main class="sheet">

  <section class="card front">
    <div class="brand">
      <span class="brand-dot"></span>
      <span class="brand-name">Keystone Trench Co</span>
    </div>
    <div class="details">
      <div class="person">
        <p class="person-name">Dale Marrow</p>
        <p class="person-role">Owner</p>
      </div>
      <div class="rule"></div>
      <ul class="contacts">
        <li>
          <svg viewBox="0 0 12 12" aria-hidden="true"><path d="M3 1l2 2.5-1.2 1.3c.6 1.4 1.7 2.5 3.1 3.1L8.2 6.7 10.7 8.7 9.6 10.8C5 10.5 1.5 7 1.2 2.4z" fill="var(--accent-blue)"/></svg>
          604-555-0182(DIG)
        </li>
        <li>
          <svg viewBox="0 0 12 12" aria-hidden="true"><rect x="1" y="2.5" width="10" height="7" fill="none" stroke="var(--accent-blue)" stroke-width="1.2"/><path d="M1 2.5l5 4 5-4" fill="none" stroke="var(--accent-blue)" stroke-width="1.2"/></svg>
          dale@keystonetrenchco.example
        </li>
        <li>
          <svg viewBox="0 0 12 12" aria-hidden="true"><circle cx="6" cy="6" r="5" fill="none" stroke="var(--accent-blue)" stroke-width="1.2"/><path d="M1 6h10M6 1c-2.5 3-2.5 7 0 10M6 1c2.5 3 2.5 7 0 10" fill="none" stroke="var(--accent-blue)" stroke-width="1"/></svg>
          www.keystonetrenchco.example
        </li>
      </ul>
    </div>
  </section>

  <section class="card back">
    <div class="brand">
      <span class="brand-dot"></span>
      <span class="brand-name">Keystone Trench Co</span>
    </div>
    <svg class="ridge-art" viewBox="0 0 530 160" preserveAspectRatio="none" role="img" aria-label="Dark grey mountain range illustration across the lower half of the card">
      <defs>
        <linearGradient id="ridgeTone" x1="0" y1="0" x2="1" y2="0">
          <stop offset="0" stop-color="var(--ridge-dark)"/>
          <stop offset="1" stop-color="var(--ridge-light)"/>
        </linearGradient>
      </defs>
      <rect width="530" height="160" fill="url(#ridgeTone)" opacity=".55"/>
    </svg>
  </section>

</main>
</body>
</html>
```